TLR PowerPoint

I am looking for a clean, corporate PowerPoint template.

I would like the following:
- title slide
- break slide
- blank slide with title (for graphs or graphics)
- an ending slide.

Target Market(s)

Business professionals, medium to large business clients.

Requirements
Must have
• Must incorporate the TLR logo in either the header or footer

```html
<!DOCTYPE html>
<html lang="en">
<head>
<meta charset="utf-8">
<title>TLR Slide – Pie Chart</title>
<link rel="stylesheet" href="https://fonts.googleapis.com/css2?family=Libre+Baskerville:wght@700&family=Open+Sans:wght@400;600&display=swap">
<style>
  :root {
    --blue-deep: #2752c2;
    --blue-mid: #3068d8;
    --blue-bright: #5a8ef0;
    --blue-light: #9dbcfa;
    --grey-light: #c0c0c0;
    --grey-mid: #808080;
    --grey-dark: #5a5a5a;
    --rule-dark: #2a1e18;
    --ink: #111522;
    --white: #ffffff;
    --watermark: rgba(255, 255, 255, 0.22);
  }
  * { margin: 0; padding: 0; box-sizing: border-box; }
  html, body { width: 1200px; height: 900px; overflow: hidden; background: var(--white); }
  .slide {
    position: relative;
    width: 1200px;
    height: 900px;
    overflow: hidden;
    background: var(--white);
    font-family: "Open Sans", Arial, sans-serif;
  }
  .slide-header {
    position: absolute;
    left: 0; top: 0;
    width: 1200px; height: 93px;
    background: linear-gradient(90deg, var(--blue-deep) 0%, #4a7fe8 45%, var(--blue-bright) 65%, var(--blue-deep) 100%);
    border-bottom: 4px solid var(--rule-dark);
  }
  .slide-title {
    position: absolute;
    left: 30px; top: 20px;
    font-family: "Libre Baskerville", Georgia, serif;
    font-weight: 700;
    font-size: 40px;
    color: var(--white);
    letter-spacing: -0.5px;
  }
  .header-name {
    position: absolute;
    right: 16px; top: 14px;
    font-family: "Open Sans", Arial, sans-serif;
    font-weight: 600;
    font-size: 50px;
    line-height: 1;
    color: var(--watermark);
  }
  .pie-chart, .footer-band {
    position: absolute;
    left: 0; top: 0;
  }
  .slice { stroke: var(--white); stroke-width: 3; }
  .slice-grey-light { fill: var(--grey-light); }
  .slice-blue-light { fill: var(--blue-light); }
  .slice-blue { fill: var(--blue-bright); }
  .slice-blue-deep { fill: var(--blue-mid); }
  .slice-grey-dark { fill: var(--grey-dark); }
  .slice-grey-mid { fill: var(--grey-mid); }
  .slice-label {
    font-family: "Open Sans", Arial, sans-serif;
    font-weight: 600;
    font-size: 20px;
    text-anchor: middle;
  }
  .label-dark { fill: var(--ink); }
  .label-light { fill: var(--white); }
  .hub-name {
    font-family: "Open Sans", Arial, sans-serif;
    font-weight: 600;
    font-size: 20px;
    fill: var(--white);
    text-anchor: middle;
  }
  .footer-name {
    position: absolute;
    left: 22px; top: 836px;
    font-family: "Open Sans", Arial, sans-serif;
    font-weight: 600;
    font-size: 28px;
    line-height: 1.2;
    color: var(--white);
  }
  .copyright {
    position: absolute;
    left: 898px; top: 854px;
    font-size: 19px;
    color: var(--white);
  }
  .page-number {
    position: absolute;
    left: 1100px; top: 831px;
    width: 50px; height: 50px;
    border: 2.5px solid var(--white);
    border-radius: 50%;
    display: flex; align-items: center; justify-content: center;
    font-weight: 600;
    font-size: 20px;
    color: var(--white);
  }
</style>
</head>
<body>
<main class="slide">
  <header class="slide-header">
    <h1 class="slide-title">Project Title here</h1>
    <div class="header-name">TLR</div>
  </header>

  <svg class="footer-band" width="1200" height="900" viewBox="0 0 1200 900">
    <defs>
      <linearGradient id="footerFill" x1="0" y1="0" x2="1" y2="0">
        <stop offset="0" stop-color="#2752c2"/>
        <stop offset="0.55" stop-color="#4a7fe8"/>
        <stop offset="0.8" stop-color="#5a8ef0"/>
        <stop offset="1" stop-color="#2752c2"/>
      </linearGradient>
    </defs>
    <path d="M0,750 C300,880 820,890 1200,722 L1200,900 L0,900 Z" fill="url(#footerFill)"/>
    <path d="M0,750 C300,880 820,890 1200,722" fill="none" stroke="#2a1e18" stroke-width="3"/>
  </svg>

  <svg class="pie-chart" width="1200" height="900" viewBox="0 0 1200 900" role="img" aria-label="Pie chart with six segments">
    <defs>
      <linearGradient id="hubFill" x1="0" y1="0" x2="0" y2="1">
        <stop offset="0" stop-color="#5a8ef0"/>
        <stop offset="1" stop-color="#2752c2"/>
      </linearGradient>
    </defs>
    <path class="slice slice-grey-light" d="M620,468 L620,176 A292,292 0 0 1 795.7,234.8 Z"/>
    <path class="slice slice-blue-light" d="M620,468 L795.7,234.8 A292,292 0 0 1 895.6,564.5 Z"/>
    <path class="slice slice-blue" d="M620,468 L895.6,564.5 A292,292 0 0 1 726.1,740.1 Z"/>
    <path class="slice slice-blue-deep" d="M620,468 L726.1,740.1 A292,292 0 0 1 345.6,567.9 Z"/>
    <path class="slice slice-grey-dark" d="M620,468 L345.6,567.9 A292,292 0 0 1 456.7,225.9 Z"/>
    <path class="slice slice-grey-mid" d="M620,468 L456.7,225.9 A292,292 0 0 1 620,176 Z"/>

    <text class="slice-label label-light" x="566" y="260">Lorem<tspan x="566" dy="30">ipsum</tspan><tspan x="566" dy="30">dolor</tspan></text>
    <text class="slice-label label-dark" x="680" y="260">Lorem<tspan x="680" dy="30">ipsum</tspan><tspan x="680" dy="30">dolor</tspan></text>
    <text class="slice-label label-dark" x="800" y="430">Lorem ipsum<tspan x="800" dy="30">dolor</tspan></text>
    <text class="slice-label label-dark" x="760" y="591">Lorem ipsum<tspan x="760" dy="30">dolor</tspan></text>
    <text class="slice-label label-dark" x="540" y="610">Lorem ipsum dolor<tspan x="540" dy="30">Lorem ipsum dolor</tspan></text>
    <text class="slice-label label-light" x="455" y="420">Lorem ipsum dolor<tspan x="455" dy="30">Lorem ipsum dolor</tspan></text>

    <circle cx="622" cy="467" r="37" fill="url(#hubFill)" stroke="#ffffff" stroke-width="3"/>
    <text class="hub-name" x="622" y="474">TLR</text>
  </svg>

  <footer>
    <p class="footer-name">Tomas Lund Advisory</p>
    <p class="copyright">Copyright text here</p>
    <div class="page-number">01</div>
  </footer>
</main>
</body>
</html>
```